Parcelwise HQ letterhead and envelope

Design a formal (8.5x11) letterhead and envelope for sales outreach and legal matters. Using design input from https://www.parcelwisehq.example/ and the attached documents.

Industry/Entity Type

Software Service

Requirements
Must have
• These 4 hex colors are our official colors:
• #355c98 [blue]
• #1eb1a2 [teal]
• #fdba12 [gold]
• #f1653b [orange]
• So no other colors besides these should be used.

```html
<!DOCTYPE html>
<html lang="en">
<head>
<meta charset="utf-8">
<title>Parcelwise HQ Letterhead</title>
<link href="https://fonts.googleapis.com/css2?family=Open+Sans:wght@400;600;700&family=Arimo:wght@700&display=swap" rel="stylesheet">
<style>
  :root {
    --brand-blue: #355c98;
    --brand-teal: #1eb1a2;
    --brand-gold: #fdba12;
    --brand-orange: #f1653b;
    --ink: #2b2b2b;
    --muted: #555a60;
    --paper: #ffffff;
    --backdrop: #e3e4e5;
    --footer-dark: #1c1c1c;
  }
  * { margin: 0; padding: 0; box-sizing: border-box; }
  html, body { width: 1200px; height: 945px; overflow: hidden; }
  body {
    background: var(--backdrop);
    font-family: "Open Sans", sans-serif;
    color: var(--ink);
  }
  .letterhead {
    position: absolute;
    left: 252px;
    top: 22px;
    width: 696px;
    height: 900px;
    background: var(--paper);
    box-shadow: 0 6px 22px rgba(0,0,0,0.12);
    overflow: hidden;
  }
  .brand {
    position: absolute;
    left: 56px;
    top: 104px;
    display: flex;
    align-items: center;
    gap: 10px;
  }
  .brand-dot {
    width: 26px; height: 26px;
    border-radius: 50%;
    border: 3px solid var(--brand-blue);
  }
  .brand-name {
    font-size: 27px;
    font-weight: 400;
    color: var(--brand-blue);
    letter-spacing: 0.2px;
  }
  .contact {
    position: absolute;
    top: 52px;
    right: 56px;
    display: flex;
    gap: 14px;
    font-size: 9px;
    line-height: 1.45;
    color: var(--muted);
  }
  .contact-lines { list-style: none; }
  .contact-lines li { display: flex; align-items: center; gap: 5px; }
  .contact-icon {
    width: 9px; height: 9px; border-radius: 50%;
    background: var(--brand-blue);
    display: inline-flex; align-items: center; justify-content: center;
  }
  .contact-address {
    border-left: 1px solid #c9ccd2;
    padding-left: 12px;
  }
  .contact-address strong {
    display: block;
    color: var(--brand-blue);
    font-weight: 700;
    font-size: 10px;
  }
  .pattern-field {
    position: absolute;
    left: 180px; top: 150px;
    width: 470px; height: 560px;
    background: radial-gradient(ellipse at center, rgba(53,92,152,0.05), rgba(253,186,18,0.03) 55%, rgba(255,255,255,0) 75%);
  }
  .letter-body {
    position: absolute;
    left: 64px;
    top: 214px;
    width: 568px;
    font-size: 13px;
    line-height: 1.32;
    color: var(--ink);
  }
  .salutation {
    font-family: "Arimo", sans-serif;
    font-weight: 700;
    font-size: 15px;
    margin-bottom: 14px;
  }
  .letter-body p { margin-bottom: 16px; }
  .signature {
    position: absolute;
    left: 64px;
    top: 690px;
    width: 150px;
    height: 58px;
    background: linear-gradient(90deg, rgba(43,43,43,0.10), rgba(43,43,43,0.03));
    border-radius: 4px;
  }
  .footer-wave {
    position: absolute;
    left: 0; bottom: 0;
    width: 696px; height: 150px;
  }
  .footer-url {
    font-family: "Open Sans", sans-serif;
    font-size: 12px;
    fill: #ffffff;
    letter-spacing: 0.4px;
  }
</style>
</head>
<body>
  <article class="letterhead">
    <header>
      <div class="brand">
        <span class="brand-dot"></span>
        <span class="brand-name">Parcelwise HQ</span>
      </div>
      <div class="contact">
        <ul class="contact-lines">
          <li><span class="contact-icon"></span>(555) 014-2290</li>
          <li><span class="contact-icon"></span>mreyes@parcelwisehq.example</li>
          <li><span class="contact-icon"></span>www.parcelwisehq.example</li>
        </ul>
        <div class="contact-address">
          <strong>Parcelwise HQ</strong>
          88 Harbor Lane<br>
          Eastfield, OR 97000
        </div>
      </div>
    </header>

    <div class="pattern-field" role="img" aria-label="Faint background pattern of small line icons"></div>

    <section class="letter-body">
      <p class="salutation">Dear Mr. Carter,</p>
      <p>Lorem Ipsum is simply dummy text of the printing and typesetting industry. Lorem Ipsum has been the industry's standard dummy text ever since the 1500s, when an unknown printer took a galley of type and scrambled it to make a type specimen book. It has survived not only five centuries, but also the leap into electronic typesetting, remaining essentially unchanged.</p>
      <p>The standard chunk of Lorem Ipsum used since the 1500s is reproduced below for those interested. Sections 1.10.32 and 1.10.33 from "de Finibus Bonorum et Malorum" by Cicero are also reproduced in their exact original form, accompanied by English versions from the 1914 translation by H. Rackham</p>
      <p>Lorem Ipsum is simply dummy text of the printing and typesetting industry. Lorem Ipsum has been the industry's standard dummy text ever since the 1500s, when an unknown printer took a galley of type and scrambled it to make a type specimen book. It has survived not only five centuries, but also the leap into electronic typesetting, remaining essentially unchanged. It was popularised in the</p>
      <p>The standard chunk of Lorem Ipsum used since the 1500s is reproduced below for those interested. Sections 1.10.32 and 1.10.33 from "de Finibus Bonorum et Malorum" by Cicero are also reproduced in their exact original form, accompanied by English versions from the 1914 translation by H. Rackham</p>
      <p>The standard chunk of Lorem Ipsum used since the 1500s is reproduced below for those interested. Sections 1.10.32 and 1.10.33 from "de Finibus Bonorum et Malorum" by Cicero are also reproduced in their exact original form.</p>
    </section>

    <div class="signature" role="img" aria-label="Handwritten signature"></div>

    <svg class="footer-wave" viewBox="0 0 696 150" preserveAspectRatio="none" aria-hidden="false">
      <path d="M0 150 L0 118 C120 60 250 30 380 40 C500 50 600 40 696 10 L696 150 Z" fill="var(--footer-dark)"/>
      <path d="M0 150 L0 128 C130 72 260 44 390 52 C510 60 610 52 696 22 L696 150 Z" fill="#ffffff"/>
      <path d="M120 150 C250 100 420 70 560 60 C620 56 665 46 696 36 L696 150 Z" fill="var(--brand-blue)"/>
      <text class="footer-url" x="470" y="128">www.parcelwisehq.example</text>
    </svg>
  </article>
</body>
</html>
```